Web Developer Needs a Business Card Design

I need a personal business card design that represents me as a web developer for potential employers. I would like the background to be a dark color on the front for contrast with my logo and name. The back will have all my information along with a smaller version of the logo. I want something with a modern look and feel, not too conservative. This will be used for potential employers and freelance work.

Industry/Entity Type

Business

Contact Information for Business Card

Front should have my logo and name. The back should have all my personal information which would include: name: Tom Varulek, phone: 570-614-3098, email: tomvarulek@quillbox.net, website url: www.tomvarulek.net, logo, web developer.

Font styles to use
Sans Serif

Requirements
Must have
• Must include my logo. The color palette base color will be the logo color.

```html
<!DOCTYPE html>
<html lang="en">
<head>
<meta charset="utf-8">
<title>Tom Varulek — Business Card</title>
<link href="https://fonts.googleapis.com/css2?family=Arimo:wght@400;700&display=swap" rel="stylesheet">
<style>
  :root {
    --stage: #141414;
    --card: #1b1b1c;
    --card-edge: #2a2a2b;
    --teal: #72cbb7;
    --white: #f4f4f4;
    --silver-light: #e6e6e6;
    --silver-dark: #6d6d6d;
  }
  *, *::before, *::after { margin: 0; padding: 0; box-sizing: border-box; }
  html, body { width: 1200px; height: 924px; overflow: hidden; background: var(--stage); }
  body { position: relative; font-family: "Arimo", Arial, sans-serif; color: var(--white); }

  .card {
    position: absolute;
    width: 525px;
    height: 300px;
    background: var(--card);
    border: 1px solid var(--card-edge);
    border-radius: 16px;
    overflow: hidden;
  }
  .card-front { left: 80px; top: 90px; }
  .card-back { left: 595px; top: 534px; }

  /* Front */
  .front-ring {
    position: absolute;
    left: 50%; top: 36px;
    width: 170px; height: 170px;
    margin-left: -85px;
    border-radius: 50%;
    border: 14px solid var(--silver-light);
    background: radial-gradient(circle at 40% 35%, #2a2a2a, #111 70%);
    box-shadow: inset 0 0 0 2px var(--silver-dark);
    display: flex;
    align-items: center;
    justify-content: center;
  }
  .front-name {
    position: absolute;
    left: 0; right: 0; top: 222px;
    text-align: center;
    font-weight: 700;
    font-size: 36px;
    letter-spacing: 0.5px;
    color: var(--silver-light);
  }
  .mark-name {
    font-weight: 700;
    font-size: 17px;
    white-space: nowrap;
  }
  .front-ring .mark-name { color: var(--silver-light); }

  /* Back */
  .brand-band {
    position: absolute;
    left: 0; right: 0; top: 46px;
    height: 92px;
    background: var(--teal);
  }
  .brand-mark {
    position: absolute;
    left: 50%; top: 20px;
    width: 146px; height: 146px;
    margin-left: -73px;
  }
  .brand-mark svg { display: block; width: 100%; height: 100%; }
  .brand-mark .mark-name {
    position: absolute;
    left: 0; right: 0; top: 50%;
    transform: translateY(-50%);
    text-align: center;
    color: var(--teal);
    font-size: 16px;
  }
  .identity {
    position: absolute;
    left: 30px; top: 200px;
    width: 250px;
    text-align: right;
  }
  .identity-name { font-weight: 700; font-size: 33px; line-height: 1.05; }
  .identity-role { font-weight: 700; font-size: 21px; margin-top: 2px; }
  .divider {
    position: absolute;
    left: 298px; top: 180px;
    width: 2px; height: 100px;
    background: var(--white);
  }
  .contact-list {
    position: absolute;
    left: 316px; top: 190px;
    list-style: none;
  }
  .contact-item {
    display: flex;
    align-items: center;
    gap: 12px;
    height: 27px;
    font-size: 15px;
    white-space: nowrap;
  }
  .contact-icon { width: 16px; height: 16px; flex: none; }
</style>
</head>
<body>

  <section class="card card-front" aria-label="Card front">
    <div class="front-ring"><span class="mark-name">Tom Varulek</span></div>
    <p class="front-name">Tom Varulek</p>
  </section>

  <section class="card card-back" aria-label="Card back">
    <div class="brand-band"></div>
    <div class="brand-mark">
      <svg viewBox="0 0 146 146" aria-hidden="true">
        <circle cx="73" cy="73" r="73" fill="#1b1b1c"/>
        <circle cx="73" cy="73" r="58.5" fill="#1b1b1c" stroke="#72cbb7" stroke-width="9"/>
      </svg>
      <span class="mark-name">Tom Varulek</span>
    </div>

    <div class="identity">
      <p class="identity-name">Tom Varulek</p>
      <p class="identity-role">Web Developer</p>
    </div>

    <div class="divider"></div>

    <ul class="contact-list">
      <li class="contact-item">
        <svg class="contact-icon" viewBox="0 0 16 16" aria-hidden="true">
          <rect x="0.5" y="0.5" width="15" height="15" rx="2" fill="#f4f4f4"/>
          <path d="M4 5.5c0 4 2.5 6.5 6.5 6.5l1-2-2-1-1 1c-1.2-.5-2-1.3-2.5-2.5l1-1-1-2z" fill="#1b1b1c"/>
        </svg>
        <span>570-614-3098</span>
      </li>
      <li class="contact-item">
        <svg class="contact-icon" viewBox="0 0 16 16" aria-hidden="true">
          <rect x="0.5" y="0.5" width="15" height="15" rx="2" fill="#f4f4f4"/>
          <rect x="3" y="5" width="10" height="7" fill="none" stroke="#1b1b1c" stroke-width="1.2"/>
          <path d="M3 5l5 4 5-4" fill="none" stroke="#1b1b1c" stroke-width="1.2"/>
        </svg>
        <span>tomvarulek@quillbox.net</span>
      </li>
      <li class="contact-item">
        <svg class="contact-icon" viewBox="0 0 16 16" aria-hidden="true">
          <rect x="0.5" y="0.5" width="15" height="15" rx="2" fill="#f4f4f4"/>
          <circle cx="8" cy="8" r="4.5" fill="none" stroke="#1b1b1c" stroke-width="1.2"/>
          <path d="M3.5 8h9M8 3.5c-2 2.5-2 6.5 0 9M8 3.5c2 2.5 2 6.5 0 9" fill="none" stroke="#1b1b1c" stroke-width="1"/>
        </svg>
        <span>www.tomvarulek.net</span>
      </li>
    </ul>
  </section>

</body>
</html>
```